Brook Refrigeration. Refrigeration and air conditioning specialists.

We need a website to promote our business. We would a modern simple design using the colours from our logo and black. We want it to be fun but proffesional.

Target Market(s)

Commercial

Number of Pages Required

4 page

Requirements
Must have
• Home Page, About Us, Services and Contact Us.
• 24/7 365 days service available.
• Brook Refrigeration's dedicated team specialises in commercial refrigeration and air conditioning equipment.
• Based in Westbrook, we cover Bayview Metro and surrounding areas.
Nice to have
• KNOWLEDGE . EXPERIENCE . PASSION in bold.
• Our experienced and highly trained technicians provide extensive knowledge and exceptional skills for your commercial refrigeration and air conditioning requirements.
• Pictures of commercial refrigeration.
Should not have
• No mention of domestic services.

```html
<!DOCTYPE html>
<html lang="en">
<head>
<meta charset="utf-8">
<title>Brook Refrigeration</title>
<link href="https://fonts.googleapis.com/css2?family=Open+Sans:wght@400;600;700;800&display=swap" rel="stylesheet">
<style>
:root{
  --green:#6cd02e;
  --green-dark:#58b41f;
  --purple:#2a1d47;
  --purple-deep:#1f1536;
  --ink:#2b2b2b;
  --muted:#7a7a7a;
  --black:#141414;
  --white:#ffffff;
  --line:#e4e4e4;
}
*{box-sizing:border-box;margin:0;padding:0}
html,body{width:1200px;height:3748px;overflow:hidden}
body{font-family:"Open Sans",Arial,sans-serif;color:var(--ink);background:var(--white);position:relative}
section,header,footer{position:relative;width:1200px;overflow:hidden}
.btn{display:inline-block;background:var(--green);color:var(--white);font-weight:600;font-size:17px;padding:10px 26px;border-radius:20px}
.section-title{font-size:34px;font-weight:600;text-align:center}

/* hero */
.hero{height:672px;background:linear-gradient(100deg,#2f3a33 0%,#4d5a52 45%,#6d7771 100%)}
.hero-scene{position:absolute;inset:0;background:linear-gradient(180deg,rgba(30,40,34,.35),rgba(20,25,22,.6))}
.nav{position:absolute;top:0;left:0;right:0;height:112px}
.logo{position:absolute;left:74px;top:30px;color:var(--green);font-weight:800;font-size:30px;line-height:1}
.menu{position:absolute;right:60px;top:44px;display:flex;gap:34px;align-items:center;font-size:17px;color:var(--white)}
.menu .active{color:var(--green)}
.menu svg{display:block}
.hero-title{position:absolute;left:88px;top:250px;color:var(--white);font-size:52px;font-weight:700;letter-spacing:1px}
.hero-tag{position:absolute;left:92px;top:322px;color:var(--white);font-size:30px;font-weight:700;letter-spacing:3px}
.hero .btn{position:absolute;left:96px;top:404px;border-radius:4px;font-size:20px;padding:12px 26px}
.hero-product{position:absolute;left:760px;top:160px;width:230px;height:470px;background:linear-gradient(90deg,#cfd6d4,#eef2f1 50%,#b8c0be);border-radius:6px}
.dots{position:absolute;left:92px;top:596px;display:flex;gap:10px}
.dots span{width:18px;height:18px;border-radius:50%;background:rgba(255,255,255,.75)}

/* welcome */
.welcome{height:600px}
.welcome-frame{position:absolute;left:96px;top:140px;width:412px;height:330px;border:3px solid #555}
.welcome-photo{position:absolute;left:112px;top:156px;width:396px;height:330px;background:linear-gradient(135deg,#dfe4e6,#f4f6f7 50%,#c9d0d3)}
.welcome-copy{position:absolute;left:552px;top:176px;width:540px}
.welcome-copy h2{font-size:34px;font-weight:600;color:var(--ink);margin-bottom:16px}
.welcome-copy h2 span{color:var(--green)}
.welcome-copy p{font-size:15px;line-height:1.7;color:var(--muted);margin-bottom:18px}

/* services */
.services{height:600px;background:linear-gradient(180deg,var(--purple) 0%,var(--purple-deep) 100%)}
.services .section-title{color:var(--white);padding-top:86px}
.title-rule{width:60px;height:3px;background:var(--green);margin:12px auto 0}
.cards{position:absolute;top:176px;left:96px;display:flex;gap:32px}
.card{width:316px;height:312px;background:var(--white);text-align:center;position:relative;padding-top:102px}
.card-icon{position:absolute;left:50%;top:-24px;margin-left:-48px;width:96px;height:96px;background:var(--green);display:flex;align-items:center;justify-content:center}
.card h3{font-size:22px;font-weight:600;margin:12px 0 14px}
.card p{font-size:14px;line-height:1.6;color:var(--muted);padding:0 34px}
.card .more{position:absolute;left:50%;bottom:-18px;transform:translateX(-50%);background:var(--white);border:1px solid var(--line);font-size:14px;padding:7px 22px;border-radius:18px}
.card.featured .more{background:var(--green);color:var(--white);border-color:var(--green)}

/* why */
.why{height:608px}
.why-copy{position:absolute;left:104px;top:176px;width:540px}
.why-copy h2{font-size:34px;font-weight:600;margin-bottom:26px}
.why-copy li{list-style:none;font-size:16px;line-height:1.6;color:var(--muted);padding-left:20px;position:relative;margin-bottom:16px}
.why-copy li::before{content:"";position:absolute;left:0;top:9px;width:9px;height:9px;border-radius:50%;background:var(--green)}
.why-copy .btn{margin-top:24px}
.why-photo{position:absolute;left:680px;top:148px;width:392px;height:320px;background:linear-gradient(135deg,#b9c4c8,#e6ebec 55%,#9ea9ad);box-shadow:10px 10px 0 #ddd}

/* testimonials */
.testimonials{height:520px;background:var(--green)}
.testimonials .section-title{padding-top:68px;color:var(--black)}
.testimonials .title-rule{background:var(--black)}
.quotes{position:absolute;left:152px;top:172px;display:flex;gap:32px}
.quote{width:418px;height:280px;background:var(--white);border-radius:10px;padding:36px 40px 0 70px;position:relative}
.avatar{position:absolute;left:-34px;top:24px;width:76px;height:76px;border-radius:50%;background:#c9c9c9;border:4px solid var(--white)}
.quote p{font-size:15px;line-height:1.75;color:var(--ink)}
.quote cite{display:block;font-style:normal;font-size:15px;margin-top:10px}

/* newsletter */
.newsletter{height:440px;text-align:center}
.newsletter .section-title{padding-top:104px}
.newsletter p{font-size:18px;margin-top:14px;color:var(--ink)}
.subscribe{display:flex;justify-content:center;margin-top:30px;gap:10px}
.subscribe .field{width:600px;height:66px;border:1px solid #cfcfcf;text-align:left;padding:20px;font-size:15px;color:var(--muted)}
.subscribe .btn{border-radius:0;height:66px;padding:20px 30px;font-size:20px}

/* footer */
.footer{height:308px;background:var(--black);color:#cfcfcf}
.cols{position:absolute;top:42px;left:92px;right:92px;display:flex}
.col h4{font-size:14px;font-weight:600;color:var(--white);margin-bottom:14px;letter-spacing:.5px}
.col li{list-style:none;font-size:13px;line-height:1.9}
.col li::before{content:"› ";color:var(--green)}
.col.contact li::before{content:""}
.social{display:flex;gap:12px}
.social span{width:30px;height:30px;background:#cfcfcf;border-radius:3px}
.copyright{position:absolute;bottom:28px;left:0;right:0;text-align:center;font-size:13px;color:#999}
</style>
</head>
<body>

<header class="hero">
  <div class="hero-scene" role="img" aria-label="Commercial refrigerated display cabinets in a store"></div>
  <nav class="nav">
    <div class="logo">Brook Refrigeration</div>
    <div class="menu">
      <span class="active">Home</span><span>About Us</span><span>Services</span><span>Contact Us</span>
      <svg width="18" height="18" viewBox="0 0 18 18"><circle cx="7.5" cy="7.5" r="5.5" fill="none" stroke="#fff" stroke-width="2"/><path d="M11.5 11.5L16 16" stroke="#fff" stroke-width="2"/></svg>
      <svg width="18" height="18" viewBox="0 0 18 18"><circle cx="9" cy="5" r="4" fill="#fff"/><path d="M1 18c0-5 4-7 8-7s8 2 8 7z" fill="#fff"/></svg>
      <svg width="20" height="18" viewBox="0 0 20 18"><path d="M1 2h3l2 10h11l2-7H6" fill="none" stroke="#fff" stroke-width="2"/><circle cx="8" cy="16" r="1.6" fill="#fff"/><circle cx="16" cy="16" r="1.6" fill="#fff"/></svg>
    </div>
  </nav>
  <h1 class="hero-title">BROOK REFRIGERATION</h1>
  <div class="hero-tag">KNOWLEDGE . EXPERIENCE . PASSION</div>
  <span class="btn">View More</span>
  <div class="hero-product" role="img" aria-label="Stainless steel double-door commercial fridge"></div>
  <div class="dots"><span></span><span></span></div>
</header>

<section class="welcome">
  <div class="welcome-frame"></div>
  <div class="welcome-photo" role="img" aria-label="Supermarket aisle with glass-door freezers"></div>
  <div class="welcome-copy">
    <h2>Welcome to <span>Brook Refrigeration</span></h2>
    <p>The point of using Lorem Ipsum is that it has a more-or-less normal distribution of letters, as opposed to using 'Content here, content here', making it look like readable English. Many desktop publishing packages and web page editors now use Lorem Ipsum as their default model text, and a search for 'lorem ipsum' will uncover many web sites still in their infancy. It is a long established fact that a reader will be distracted by the readable content of a page when looking at its layout.</p>
    <span class="btn">Read More</span>
  </div>
</section>

<section class="services">
  <h2 class="section-title">Our Service</h2>
  <div class="title-rule"></div>
  <div class="cards">
    <div class="card">
      <div class="card-icon"><svg width="44" height="52" viewBox="0 0 44 52"><rect x="3" y="2" width="38" height="48" rx="3" fill="none" stroke="#fff" stroke-width="3"/><path d="M3 20h38M10 9v6M10 26v10" stroke="#fff" stroke-width="3"/></svg></div>
      <h3>Porro quisquam</h3>
      <p>It is a long established fact that a reader will be distracted by the readable content of a page</p>
      <span class="more">Read more</span>
    </div>
    <div class="card featured">
      <div class="card-icon"><svg width="50" height="50" viewBox="0 0 50 50"><circle cx="25" cy="25" r="20" fill="none" stroke="#fff" stroke-width="3"/><path d="M25 12v26M14 19l22 12M14 31l22-12" stroke="#fff" stroke-width="3"/></svg></div>
      <h3>Dolorem ipsum</h3>
      <p>It is a long established fact that a reader will be distracted by the readable content of a page</p>
      <span class="more">Read more</span>
    </div>
    <div class="card">
      <div class="card-icon"><svg width="40" height="52" viewBox="0 0 40 52"><rect x="3" y="2" width="34" height="48" rx="5" fill="none" stroke="#fff" stroke-width="3"/><rect x="9" y="9" width="22" height="30" fill="#fff"/></svg></div>
      <h3>Neque quisquam</h3>
      <p>It is a long established fact that a reader will be distracted by the readable content of a page</p>
      <span class="more">Read more</span>
    </div>
  </div>
</section>

<section class="why">
  <div class="why-copy">
    <h2>Why Choose Us</h2>
    <ul>
      <li>24/7 365 days service available.</li>
      <li>Brook Refrigeration's dedicated team specialises in commercial refrigeration and air conditioning equipment.</li>
      <li>Based in Westbrook, we cover Bayview Metro and surrounding areas.</li>
    </ul>
    <span class="btn">Read More</span>
  </div>
  <div class="why-photo" role="img" aria-label="Row of commercial glass-door display freezers"></div>
</section>

<section class="testimonials">
  <h2 class="section-title">Testimonials</h2>
  <div class="title-rule"></div>
  <div class="quotes">
    <div class="quote">
      <div class="avatar" role="img" aria-label="Customer portrait"></div>
      <p>" The point of using Lorem Ipsum is that it has a more-or-less normal distribution of letters, as opposed to using 'Content here, content here', making it look like readable English. Many desktop publishing packages and web page editors now use Lorem Ipsum "</p>
      <cite>– Mara Quill</cite>
    </div>
    <div class="quote">
      <div class="avatar" role="img" aria-label="Customer portrait"></div>
      <p>" The point of using Lorem Ipsum is that it has a more-or-less normal distribution of letters, as opposed to using 'Content here, content here', making it look like readable English. Many desktop publishing packages and web page editors now use Lorem Ipsum "</p>
      <cite>– Dana Holt</cite>
    </div>
  </div>
</section>

<section class="newsletter">
  <h2 class="section-title">Newsletter</h2>
  <p>Neque porro quisquam est qui dolorem ipsum quia dolor</p>
  <div class="subscribe"><div class="field">Your@email.com</div><span class="btn">Subscribe</span></div>
</section>

<footer class="footer">
  <div class="cols">
    <div class="col" style="width:250px">
      <h4>INFORMATION</h4>
      <ul><li>Privacy Policy</li><li>Your Account</li><li>Advanced Search</li><li>Contact Us</li></ul>
    </div>
    <div class="col" style="width:200px">
      <h4>LINKS</h4>
      <ul><li>Home</li><li>About us</li><li>Products</li><li>Review</li></ul>
    </div>
    <div class="col contact" style="width:366px">
      <h4>CONTACT US</h4>
      <ul><li>Address : 12 Harbour Lane, Westbrook WA 6027, Australia</li><li>Phone : (08) 5550 1234 / 0400 555 019</li><li>Email : hello@brookcool.example</li></ul>
    </div>
    <div class="col">
      <h4>FOLLOW US OUT THERE</h4>
      <div class="social"><span></span><span></span><span></span><span></span></div>
    </div>
  </div>
  <div class="copyright">Copyright © 2018. All Rights Reserved</div>
</footer>

</body>
</html>
```